New banner graphics for Tondix.com website

I've developed a software tool that helps businesses ensure they are working on their most valuable and important work.

I would like a banner graphic for my home page (www.tondix.com) that can somehow capture the value of focus and intentional outcomes.

I had an initial thought of a starry sky that shifts focus to a few bright stars, but while that might sound ok, I think my idea is lame hence I'm coming to you guys.

My sites two primary colors are a soft purple and gray.
#919EC1(purple)
#9E9E9E (gray)

Target Market(s)

B2B for enterprises. Typical customers are CFOs, CIOs/Heads of IT

Industry/Entity Type

Business Software

Number of Pages Required

1 page

Font styles to use
Sans Serif

Colors
b8a6cd
cedeed

Requirements
Must have
• I use Divi as my Wordpress theme and the current main landing page can be seen at www.tondix.com.
• My logo colors are:
• #919EC1(purple)
• #9E9E9E (gray)
Should not have
• Lots of distraction or visual "noise". I want to re-enforce the message that my software is focused on their business and not my products or website.

```html
<!DOCTYPE html>
<html lang="en">
<head>
<meta charset="UTF-8">
<title>Is Your Business Strategy</title>
<link rel="stylesheet" href="https://fonts.googleapis.com/css2?family=Roboto:wght@700&family=Raleway:ital,wght@0,700;0,800;1,700&display=swap">
<style>
  :root {
    --sky-deep: #0d1233;
    --sky-mid: #2a2f6b;
    --sky-violet: #4b3f7e;
    --sky-haze: #6f6d9f;
    --text-light: #ffffff;
    --frame-line: rgba(255, 255, 255, 0.85);
  }
  html, body {
    margin: 0;
    padding: 0;
    width: 1200px;
    height: 675px;
    overflow: hidden;
    background: var(--sky-deep);
  }
  .banner {
    position: relative;
    width: 1200px;
    height: 675px;
    overflow: hidden;
    color: var(--text-light);
  }
  .banner__sky {
    position: absolute;
    inset: 0;
    background:
      radial-gradient(ellipse 420px 260px at 28% 82%, rgba(150, 150, 200, 0.45), transparent 70%),
      radial-gradient(ellipse 380px 220px at 58% 42%, rgba(120, 90, 150, 0.35), transparent 70%),
      radial-gradient(ellipse 300px 200px at 22% 18%, rgba(110, 120, 190, 0.35), transparent 70%),
      linear-gradient(160deg, var(--sky-mid) 0%, var(--sky-deep) 35%, var(--sky-violet) 60%, var(--sky-mid) 80%, var(--sky-deep) 100%);
  }
  .headline {
    position: absolute;
    top: 130px;
    left: 0;
    width: 1234px;
    display: flex;
    justify-content: center;
    align-items: center;
    gap: 38px;
    font-family: "Roboto", Arial, sans-serif;
    font-weight: 700;
    font-size: 40px;
    text-shadow: 0 1px 4px rgba(0, 0, 0, 0.35);
  }
  .headline__lead {
    white-space: nowrap;
  }
  .headline__framed {
    border: 1px solid var(--frame-line);
    height: 66px;
    width: 440px;
    display: flex;
    align-items: center;
    justify-content: center;
    white-space: nowrap;
    box-sizing: border-box;
  }
  .contrasts {
    position: absolute;
    top: 302px;
    left: 0;
    width: 1234px;
    margin: 0;
    padding: 0;
    list-style: none;
    text-align: center;
    font-family: "Raleway", Arial, sans-serif;
    font-size: 25px;
    line-height: 34px;
    text-shadow: 0 1px 4px rgba(0, 0, 0, 0.4);
    white-space: nowrap;
  }
  .contrasts__strong {
    font-weight: 800;
  }
  .contrasts__or {
    font-family: "Roboto", Arial, sans-serif;
    font-weight: 400;
    font-size: 22px;
    margin: 0 14px;
  }
  .contrasts__weak {
    font-weight: 700;
    font-style: italic;
  }
</style>
</head>
<body>
  <div class="banner">
    <div class="banner__sky" role="img" aria-label="Night sky full of stars with a violet and blue milky way"></div>

    <h1 class="headline">
      <span class="headline__lead">Is Your</span>
      <span class="headline__framed">“ Business Strategy ”</span>
    </h1>

    <ul class="contrasts">
      <li><span class="contrasts__strong">WRITTEN DOWN</span><span class="contrasts__or">or</span><span class="contrasts__weak">LOOSE THOUGHTS – ON THE BEST OF DAYS</span></li>
      <li><span class="contrasts__strong">DRIVING PROJECTS</span><span class="contrasts__or">or</span><span class="contrasts__weak">JUST A SET OF SLIDES TACKED TO WALLS</span></li>
      <li><span class="contrasts__strong">SHARED WITH THE TEAM</span><span class="contrasts__or">or</span><span class="contrasts__weak">KEPT TOP SECRET JUST TO BE SAFE</span></li>
      <li><span class="contrasts__strong">MEASURABLE</span><span class="contrasts__or">or</span><span class="contrasts__weak">MORE ART THAN SCIENCE</span></li>
    </ul>
  </div>
</body>
</html>
```